Video Editing Website - Wordpress Design Project

Hi There
I am setting up a Tribute Funeral Video and Home Video Editing Website for my Company. "Reel Harbor". This is to assist people with putting together their Videos and Photos with music to show at a Funeral or for Family Memories. I already have a domain www.reelharbor.com.au, but I have no host yet.

Some websites that already do this are http://www.quietlantern.com.au/tributes, http://www.cobaltframeworks.com.au/services/funeral-tribute-videos.html, and http://www.sundialkeepsakes.com.au/
These are examples not to cpy, but to get an idea of what I am offering so you can design accordingly.

I have a logo which is attached. You will see that the logo is mainly blue, so I would appreciate a website with that colour on the pages, but not ALL over the page.

I would like to upload videos occasionally from clipnest.com so I would appreciate that option incorporated.

Thank you lots.
Gareth

Target Market(s)

Families predominately in the 25-60 age range

Industry/Entity Type

It Company

Requirements
Must have
• *Ability to upload Videos from clipnest.com
*Ability for me to edit the content whenever I need to
*A contact page to send email messages to me

```html
<!DOCTYPE html>
<html lang="en">
<head>
<meta charset="utf-8">
<title>Reel Harbor – Tribute Funeral Videos</title>
<link href="https://fonts.googleapis.com/css2?family=Source+Sans+3:ital,wght@0,300;0,400;0,600;1,300&display=swap" rel="stylesheet">
<style>
  :root{
    --brand:#1f5cab;
    --nav-top:#2f7ad6;
    --nav-bottom:#1a4ea8;
    --orange:#f7941d;
    --orange-dark:#e67a0a;
    --text:#707070;
    --heading:#4a4a4a;
    --sky:#cfe8fb;
    --sky-deep:#8cc8f2;
    --footer:#1d4d96;
    --line:#dfe7ef;
  }
  *{margin:0;padding:0;box-sizing:border-box}
  html,body{width:943px;height:1200px;overflow:hidden}
  body{
    position:relative;
    font-family:"Source Sans 3",sans-serif;
    color:var(--text);
    background:linear-gradient(90deg,var(--sky-deep) 0,var(--sky) 4%,#eef7fe 8%,#eef7fe 92%,var(--sky) 96%,var(--sky-deep) 100%);
  }
  .abs{position:absolute}

  .header{position:absolute;left:0;top:0;width:943px;height:112px;background:linear-gradient(#ffffff,#f2f2f2)}
  .brand{position:absolute;left:62px;top:28px;display:flex;align-items:center;gap:10px}
  .brand-dot{width:52px;height:52px;border-radius:50%;background:var(--brand)}
  .brand-name{font-size:30px;font-weight:400;color:var(--brand)}
  .phone{position:absolute;left:730px;top:36px;font-size:19px;color:var(--brand);display:flex;align-items:center;gap:6px}
  .cta{position:absolute;left:735px;top:69px;width:142px;height:28px;border-radius:3px;background:linear-gradient(var(--orange),var(--orange-dark));color:#fff;font-size:13.5px;display:flex;align-items:center;justify-content:center}

  .nav{position:absolute;left:0;top:112px;width:943px;height:43px;background:linear-gradient(var(--nav-top),var(--nav-bottom));display:flex;padding-left:57px}
  .nav a{color:#fff;text-decoration:none;font-size:14px;display:flex;align-items:center;justify-content:center;border-right:1px solid rgba(255,255,255,.25)}
  .nav a:last-child{border-right:none}

  .panel{position:absolute;left:54px;top:171px;width:835px;height:1029px;background:#fff;border-radius:14px 14px 0 0}

  .hero{position:absolute;left:65px;top:183px;width:813px;height:311px;border-radius:16px;overflow:hidden;border:1px solid #dcdcdc;background:linear-gradient(90deg,#f4f4f6,#e9eaee)}
  .hero-photo{position:absolute;right:0;top:0;width:609px;height:311px;background:
    radial-gradient(ellipse at 60% 55%,#fbfbf2 0,#eef0d8 30%,rgba(110,150,60,.55) 62%,rgba(233,234,238,0) 80%)}
  .hero h1{position:absolute;left:62px;top:78px;font-size:31px;font-weight:400;color:var(--brand);white-space:nowrap}
  .hero h2{position:absolute;left:62px;top:113px;font-size:19.5px;font-weight:400;color:var(--brand);white-space:nowrap}
  .hero p{position:absolute;left:62px;top:143px;width:285px;font-size:10.5px;font-weight:300;line-height:18.5px;color:var(--brand)}
  .hero .arrows{position:absolute;left:64px;top:191px}

  .card{position:absolute;top:507px;width:258px;height:143px;border:1px solid var(--line);border-radius:5px;background:linear-gradient(#fff,#f1f6fb);padding:20px 0 0 23px}
  .card h3{font-size:16.5px;font-weight:400;color:var(--brand);margin-bottom:6px}
  .card p{font-size:10.2px;font-weight:300;line-height:16.3px;color:var(--brand);width:220px}
  .btn-blue{display:inline-flex;align-items:center;justify-content:center;margin-top:10px;width:81px;height:25px;border-radius:3px;background:linear-gradient(#2566c2,#123f8c);color:#fff;font-size:10.5px}

  .welcome{position:absolute;left:83px;top:690px;width:505px}
  .welcome h2{font-size:22px;font-weight:300;color:var(--heading)}
  .welcome .lead{font-size:13.5px;font-weight:300;color:var(--heading);margin-top:4px}
  .welcome p{font-size:10.6px;font-weight:300;line-height:18.8px;margin-top:4px}

  .divider{position:absolute;left:605px;top:689px;width:1px;height:359px;background:#e4e4e4}

  .side-title{position:absolute;font-size:18px;font-weight:300;color:var(--heading)}
  .thumb{position:absolute;width:70px;height:59px}

  .feature h3{position:absolute;font-size:18px;font-weight:300;color:var(--orange-dark)}
  .feature .img{position:absolute;width:98px;height:109px}
  .feature p{position:absolute;width:138px;font-size:10.6px;font-weight:300;line-height:18.8px}
  .btn-grey{position:absolute;width:81px;height:25px;border-radius:3px;background:linear-gradient(#d6d6d6,#b3b3b3);color:#fff;font-size:10.5px;display:flex;align-items:center;justify-content:center}

  .quote{position:absolute;left:642px;top:929px;width:225px;font-size:11px;line-height:19px;font-style:italic;font-weight:300}
  .author{position:absolute;left:642px;top:1013px;font-size:11.5px;font-weight:300;color:var(--heading)}

  .footer-wave{position:absolute;left:0;top:1070px}
  .copyright{position:absolute;left:52px;top:1165px;font-size:10px;font-weight:300;color:#c9d8ef}
</style>
</head>
<body>

<header class="header">
  <div class="brand">
    <span class="brand-dot"></span>
    <span class="brand-name">Reel Harbor</span>
  </div>
  <div class="phone">
    <svg width="20" height="14" viewBox="0 0 20 14" aria-hidden="true"><path d="M1 5c3-4 15-4 18 0l-3 2-2-2H6L4 7z M5 7h10l2 6H3z" fill="#9a9a9a"/></svg>
    555.014.2290
  </div>
  <div class="cta">Submit Video Needs</div>
</header>

<nav class="nav">
  <a style="width:71px">HOME</a>
  <a style="width:96px">ABOUT US</a>
  <a style="width:90px">SERVICES</a>
  <a style="width:76px">PRICES</a>
  <a style="width:105px">RESOURCES</a>
  <a style="width:90px">SAMPLES</a>
  <a style="width:64px">TIPS</a>
  <a style="width:57px">FAQ</a>
  <a style="width:92px">SUPPORT</a>
  <a style="width:92px">CONTACT</a>
</nav>

<div class="panel"></div>

<section class="hero">
  <div class="hero-photo" role="img" aria-label="Bouquet of white lilies and roses with green ferns"></div>
  <h1>Tribute Funeral Videos</h1>
  <h2>Nunc tempus felis vitae urna</h2>
  <p>Mauris vel lacus vitae felis vestibulum volutpat. Etiam est nunc, venenatis in, tristique eu, imperdiet ac</p>
  <svg class="arrows" width="28" height="20" viewBox="0 0 28 20" aria-hidden="true">
    <path d="M10 2 3 10l7 8M18 2l7 8-7 8" fill="none" stroke="#8aa0c8" stroke-width="1.6"/>
  </svg>
</section>

<div class="card" style="left:68px">
  <h3>Digital Tribute Packages</h3>
  <p>Phasellus felis dolor, scelerisque a, tempus eget, lobortis id, libero. Donec scelerisque leo ac risus. Praesent sit amet est. In dictum</p>
  <span class="btn-blue">CLICK HERE</span>
</div>
<div class="card" style="left:338px">
  <h3>Assisted Edit Tribute Package</h3>
  <p>Phasellus felis dolor, scelerisque a, tempus eget, lobortis id, libero. Donec scelerisque leo ac risus. Praesent sit amet est. In dictum</p>
  <span class="btn-blue">CLICK HERE</span>
</div>
<div class="card" style="left:606px">
  <h3>Other Tribute Packages</h3>
  <p>Phasellus felis dolor, scelerisque a, tempus eget, lobortis id, libero. Donec scelerisque leo ac risus. Praesent sit amet est. In dictum</p>
  <span class="btn-blue">CLICK HERE</span>
</div>

<section class="welcome">
  <h2>Welcome to Our Website Mainpage..</h2>
  <div class="lead">Phasellus felis dolor, scelerisque a, tempus eget, lobortis id, libero.</div>
  <p>Donec scelerisque leo ac risus. Praesent sit amet est. In dictum, dolor eu dictum porttitor, enim felis viverra mi, eget luctus massa purus quis odio. Etiam nulla massa, pharetra facilisis, volutpat in, imperdiet sit ame</p>
  <p style="margin-top:8px">Aliquam nec erat at purus cursus interdum. Vestibulum ligula augue, bibendum accumsan, vestibulum ut, commodo a, mi. Morbi ornare gravida elit. Integer congue, augue et malesuada iaculis, ipsum dui aliquet felis, at cursus magna nisl nec elit. Donec iaculis diam a nisi accumsan viverra.</p>
</section>

<div class="divider"></div>

<h3 class="side-title" style="left:626px;top:682px">Sample Gallery</h3>
<div class="thumb" style="left:626px;top:715px;background:linear-gradient(135deg,#8a6d55,#e9e4e2)" role="img" aria-label="Heart-shaped memorial stone"></div>
<div class="thumb" style="left:706px;top:715px;background:linear-gradient(#7f9a5c,#6e6a5a)" role="img" aria-label="Row of stone crosses in a cemetery"></div>
<div class="thumb" style="left:786px;top:715px;background:linear-gradient(#6f7f5a,#9a8f80)" role="img" aria-label="Graves with flowers"></div>
<div class="thumb" style="left:626px;top:783px;background:linear-gradient(#c9a23a,#4f6a34)" role="img" aria-label="Autumn trees over a cemetery"></div>
<div class="thumb" style="left:706px;top:783px;background:radial-gradient(circle,#e8f4f4,#5aa0a8)" role="img" aria-label="Crucifix against a bright sky"></div>
<div class="thumb" style="left:786px;top:783px;background:linear-gradient(#5a4a3a,#e8822a 60%,#3f6a2a)" role="img" aria-label="Orange floral wreath on a grave"></div>

<h3 class="side-title" style="left:632px;top:896px">Testimonials</h3>
<svg class="abs" style="left:626px;top:928px" width="14" height="10" viewBox="0 0 14 10" aria-hidden="true"><path d="M1 9 3 1h3L4 9zm6 0 2-8h3l-2 8z" fill="#888"/></svg>
<p class="quote">Duis tincidunt lectus quis dui viverra vestibulum. Suspendisse vulputate aliquam dui. Nulla elementum dui ut augue. Aliquam vehicula mi at mauris.
  <svg width="14" height="10" viewBox="0 0 14 10" aria-hidden="true"><path d="M4 1 2 9h3l2-8zm6 0-2 8h3l2-8z" fill="#555"/></svg></p>
<div class="author">By Author Name</div>

<section class="feature">
  <h3 style="left:84px;top:893px">Videography</h3>
  <div class="img" style="left:85px;top:925px;background:radial-gradient(circle at 60% 60%,#f2a23a,#7a2a08 60%,#2a0d04)" role="img" aria-label="Candles glowing beside an angel statue"></div>
  <p style="left:193px;top:920px">Donec iaculis diam a nisi accumsan viverra. Duis sed tellus et tortor vestibulum gravida. Praesent elementum elit at tellus. Curabitur metus ipsum, luctus eu</p>
  <span class="btn-grey" style="left:193px;top:1041px">CLICK HERE</span>

  <h3 style="left:353px;top:893px">Audio Visual</h3>
  <div class="img" style="left:353px;top:925px;background:linear-gradient(#bcd6ee,#f0e8d8 55%,#e0b04a 70%,#8a9a5a)" role="img" aria-label="Golden temple tower against a blue sky"></div>
  <p style="left:462px;top:920px">Donec iaculis diam a nisi accumsan viverra. Duis sed tellus et tortor vestibulum gravida. Praesent elementum elit at tellus. Curabitur metus ipsum, luctus eu</p>
  <span class="btn-grey" style="left:460px;top:1041px">CLICK HERE</span>
</section>

<svg class="footer-wave" width="943" height="130" viewBox="0 0 943 130" aria-hidden="true">
  <path d="M0 10 C200 80 420 80 600 58 C760 40 880 45 943 55 V130 H0 Z" fill="var(--footer)"/>
</svg>
<div class="copyright">© 2013 Company Name.&nbsp; All right reserved.&nbsp; Term of Use</div>

</body>
</html>
```